cryotherapy business . Whole Body Cryotherapy, Localised Cryotherapy, Cryofacials

Need home page plus services, about, pricing, online booking, contact and blog page

I want something slick, hip and professional. Our studio colours are duck egg blue, white and grey

I would also like a social media scroll at the bottom of every page

I will upload some web designs that I like the look of

Target Market(s)

Men and Women 25-45

Industry/Entity Type

Health And Wellness

Coding

Coded - Design and coding required

Number of Pages Required

5+ page

Font styles to use
Serif
Sans Serif

Requirements
Must have
• Must be eye catching and easy to navigate
Nice to have
• animation
Should not have
• Not sure what the site should not have. I am fairly open to ideas as this is a brand new business.

```html
<!DOCTYPE html>
<html lang="en">
<head>
<meta charset="utf-8">
<title>Glacia — Integrated Cryotherapy</title>
<link href="https://fonts.googleapis.com/css2?family=Nunito:ital,wght@0,300;0,400;0,600;0,700;1,400&family=Raleway:wght@100;200;300;400&family=Roboto+Condensed:wght@700&display=swap" rel="stylesheet">
<style>
:root{
  --hero-deep:#0b2f8c;
  --hero-mid:#1c4fb3;
  --hero-light:#5f8fd6;
  --duck:#9cc6d2;
  --duck-dark:#7fb0c0;
  --grey:#6b6b6b;
  --grey-dark:#5c5c5c;
  --ink:#222;
  --body:#555;
  --line:#d9d9d9;
  --white:#fff;
  --star:#c9d400;
  --ghost:#ececec;
}
*{margin:0;padding:0;box-sizing:border-box}
html,body{width:1200px;height:4024px;overflow:hidden;background:var(--white)}
body{position:relative;font-family:'Nunito',sans-serif;color:var(--ink)}
.abs{position:absolute}
.center{left:0;width:1200px;text-align:center}

/* hero */
.hero{position:absolute;left:0;top:0;width:1200px;height:760px;
  background:radial-gradient(ellipse at 70% 75%,#8fb2e6 0%,rgba(143,178,230,0) 45%),linear-gradient(180deg,var(--hero-deep) 0%,var(--hero-mid) 55%,var(--hero-light) 100%)}
.brand{font-family:'Raleway',sans-serif;font-weight:300;color:#cfd8e6;font-size:34px;letter-spacing:5px}
.nav{top:54px;left:486px;display:flex;gap:0}
.nav a{color:#fff;text-decoration:none;font-size:12.5px;font-weight:600;margin-right:30px;letter-spacing:.3px}
.kicker{font-family:'Raleway',sans-serif;color:#fff;font-size:17px;letter-spacing:3px}
.cold{font-family:'Raleway',sans-serif;font-weight:100;color:#fff;font-size:150px;letter-spacing:34px;line-height:1}
.play{left:573px;top:484px;width:54px;height:54px;border:4px solid #fff;border-radius:50%}
.play::after{content:"";position:absolute;left:18px;top:13px;border-left:18px solid #fff;border-top:10px solid transparent;border-bottom:10px solid transparent}

/* about */
h2{font-weight:400;font-size:36px;color:var(--ink)}
.about-text{left:145px;top:862px;width:440px;font-size:12.5px;line-height:29.5px;color:var(--body)}
.pill{border-radius:24px;color:#fff;font-size:14px;text-align:center;letter-spacing:.5px}
.pill .dot{display:inline-block;width:12px;height:12px;border-radius:50%;background:#fff;vertical-align:-1px;margin-left:6px}
.ghost{font-family:'Roboto Condensed',sans-serif;font-weight:700;color:var(--ghost);line-height:1}

/* faq */
.faq-item{width:422px;height:48px;border:2px solid var(--line);font-size:13.5px;color:#333;padding:13px 16px}
.faq-item .plus{position:absolute;right:8px;top:9px;width:26px;height:26px;background:var(--duck);}
.faq-item .plus::after{content:"+";position:absolute;left:0;top:2px;width:26px;text-align:center;color:#fff;font-size:16px;font-weight:700}

/* pricing */
.card{background:#fff;box-shadow:0 6px 14px rgba(0,0,0,.12)}
.card-head{position:absolute;left:0;top:0;width:100%;text-align:center;color:#fff;font-weight:700}
.card .row{position:absolute;font-size:12.5px;color:#444}
.card .price{position:absolute;font-size:17px;font-weight:700;color:#333}
.card .buy{position:absolute;height:20px;border:1.5px solid var(--duck);color:var(--duck);font-size:9px;text-align:center;line-height:17px;letter-spacing:.5px}
.card .book{position:absolute;left:0;width:100%;text-align:center;color:var(--grey);font-weight:600}
.arrow-btn{width:32px;height:32px;border:1.5px solid #fff;border-radius:50%;color:#fff;font-size:18px;text-align:center;line-height:28px}

/* testimonials */
.quote{width:210px;font-size:11.5px;line-height:22px;font-style:italic;color:#888}
.quote .mark{color:#bbb;font-size:16px;margin-right:6px}
.who{font-size:9.5px;font-weight:700;color:#333;text-transform:uppercase}
.role{font-size:9px;font-style:italic;color:#333}
.stars{color:var(--star);font-size:17px;letter-spacing:4px}
.avatar{width:68px;height:68px;border-radius:50%;border:3px solid #eee;background:linear-gradient(150deg,#d9cfc7,#9a8c82)}

/* contact */
.contact-text{color:#fff;font-size:12.5px;line-height:19.5px}
.contact-head{color:#fff;font-size:15px;font-weight:700;letter-spacing:.5px}
.ring-icon{width:62px;height:62px;border-radius:50%;border:4px solid var(--duck);background:#fff}
.link{color:#fff;font-size:12.5px;text-decoration:underline;font-weight:600}
.social{width:38px;height:38px;border:2px solid #fff;border-radius:50%}
.copy{color:#fff;font-size:11.5px}
</style>
</head>
<body>

<!-- HERO -->
<div class="hero" role="img" aria-label="Swirling blue cold vapour background"></div>
<div class="abs brand" style="left:145px;top:42px;">GLACIA</div>
<nav class="abs nav"><a>HOME</a><a>SERVICES</a><a>ABOUT</a><a>PRICING</a><a>ONLINE BOOKING</a><a>CONTACT &amp; BLOG</a></nav>
<div class="abs center kicker" style="top:188px;">THE POWER OF</div>
<div class="abs center cold" style="top:232px;padding-left:34px;">COLD</div>
<div class="abs center kicker" style="top:409px;letter-spacing:5px;">INTEGRATED CRYOTHERAPY</div>
<div class="abs play"></div>
<svg class="abs" style="left:0;top:560px" width="1200" height="220" viewBox="0 0 1200 220">
  <path d="M0 40 C300 150 700 170 1200 30 L1200 220 L0 220Z" fill="#fff"/>
  <path d="M0 60 C320 150 720 160 1200 40" fill="none" stroke="#8fc3cf" stroke-width="10"/>
  <path d="M0 80 C330 165 740 175 1200 55" fill="none" stroke="#cfe6ec" stroke-width="8"/>
  <path d="M0 98 C340 178 760 190 1200 70" fill="none" stroke="#e6eef6" stroke-width="6"/>
</svg>

<!-- ABOUT -->
<h2 class="abs" style="left:145px;top:800px;">WHAT IS CRYOTHERAPY?</h2>
<p class="abs about-text">Originally invented by doctors as a powerful anti-inflammatory tool, cryotherapy is a quick, noninvasive process that exposes your body to extreme cold of up to -250°F. This sudden drop in temperature increases circulation and pumps reoxygenated and nutrient enriched blood back into the bloodstream reducing pain &amp; inflammation and alleviating sore muscles. It's also known to release 'feel good'</p>
<div class="abs pill" style="left:145px;top:1068px;width:168px;height:44px;line-height:44px;background:var(--duck);">READ MORE<span class="dot"></span></div>
<svg class="abs" style="left:666px;top:784px" width="400" height="400" viewBox="0 0 400 400" role="img" aria-label="Cryotherapy chamber product shot framed by a pale blue ring">
  <circle cx="200" cy="200" r="185" fill="none" stroke="#c9dbe1" stroke-width="26"/>
  <circle cx="200" cy="200" r="150" fill="url(#chamber)"/>
  <defs><linearGradient id="chamber" x1="0" y1="0" x2="1" y2="1"><stop offset="0" stop-color="#f1f4f7"/><stop offset="1" stop-color="#b9c8d8"/></linearGradient></defs>
</svg>
<div class="abs ghost" style="left:8px;top:1160px;font-size:108px;">ABOUT</div>

<!-- WHAT TO EXPECT -->
<svg class="abs" style="left:0;top:1250px" width="1200" height="480" viewBox="0 0 1200 480">
  <path d="M0 70 C300 0 800 -10 1200 60 L1200 380 C900 450 300 450 0 385Z" fill="var(--grey)"/>
  <path d="M880 14 C1000 22 1100 40 1200 60" fill="none" stroke="var(--duck)" stroke-width="8"/>
  <path d="M0 380 C300 446 900 446 1200 376" fill="none" stroke="var(--duck)" stroke-width="8"/>
</svg>
<div class="abs ghost" style="left:903px;top:1312px;font-size:108px;color:#5e5e5e;">WHAT</div>
<h2 class="abs center" style="top:1355px;color:#fff;">WHAT TO EXPECT</h2>
<p class="abs center" style="top:1418px;color:#fff;font-size:13.5px;line-height:25px;">As a first time client, we'll ask you for some information about your medical history and what your goals<br>are.Then once you've signed the waiver, you'll be ready to start.</p>
<svg class="abs" style="left:140px;top:1485px" width="920" height="360" viewBox="0 0 920 360">
  <defs>
    <clipPath id="c1"><circle cx="179" cy="179" r="141"/></clipPath>
    <clipPath id="c2"><circle cx="458" cy="179" r="141"/></clipPath>
    <clipPath id="c3"><circle cx="740" cy="179" r="141"/></clipPath>
  </defs>
  <circle cx="179" cy="179" r="163" fill="#fff" stroke="var(--duck)" stroke-width="9"/>
  <circle cx="740" cy="179" r="163" fill="#fff" stroke="var(--duck)" stroke-width="9"/>
  <circle cx="458" cy="179" r="163" fill="#fff" stroke="var(--duck)" stroke-width="9"/>
  <g clip-path="url(#c1)"><rect x="30" y="30" width="300" height="300" fill="#d8cdc4" role="img" aria-label="Before: client warming hands in knit mittens"/><rect x="30" y="248" width="300" height="90" fill="#6f6f6f"/></g>
  <g clip-path="url(#c2)"><rect x="310" y="30" width="300" height="300" fill="#9a9ba1" role="img" aria-label="During: client inside the vapour-filled chamber"/><rect x="310" y="30" width="300" height="60" fill="#6f6f6f"/></g>
  <g clip-path="url(#c3)"><rect x="590" y="30" width="300" height="300" fill="#c5c1c9" role="img" aria-label="After: client stepping out wrapped in a towel"/><rect x="590" y="248" width="300" height="90" fill="#6f6f6f"/></g>
  <text x="179" y="289" fill="#fff" font-family="Nunito,sans-serif" font-size="20" text-anchor="middle">BEFORE</text>
  <text x="458" y="68" fill="#fff" font-family="Nunito,sans-serif" font-size="20" text-anchor="middle">DURING</text>
  <text x="740" y="289" fill="#fff" font-family="Nunito,sans-serif" font-size="20" text-anchor="middle">AFTER</text>
</svg>

<!-- FAQ -->
<h2 class="abs center" style="top:1908px;">FREQUENTLY ASKED QUESTIONS</h2>
<div class="abs faq-item" style="left:167px;top:1993px;">What is Cryotherapy?<span class="plus"></span></div>
<div class="abs faq-item" style="left:611px;top:1993px;">Why should I do Cryotherapy?<span class="plus"></span></div>
<div class="abs faq-item" style="left:167px;top:2055px;">How does Cryotherapy work?<span class="plus"></span></div>
<div class="abs faq-item" style="left:611px;top:2055px;">Should I do Cryo before or after I work out?<span class="plus"></span></div>
<div class="abs faq-item" style="left:167px;top:2117px;">How often should I do Cryotherapy?<span class="plus"></span></div>
<div class="abs faq-item" style="left:611px;top:2117px;">Sed ut perspiciatis unde omnis iste natus ?<span class="plus"></span></div>
<div class="abs faq-item" style="left:167px;top:2179px;">How often should I do Cryotherapy?<span class="plus"></span></div>
<div class="abs faq-item" style="left:611px;top:2179px;">Sed ut perspiciatis unde omnis iste natus ?<span class="plus"></span></div>
<div class="abs pill" style="left:516px;top:2272px;width:168px;height:44px;line-height:44px;background:var(--grey);">VIEW MORE<span class="dot"></span></div>
<div class="abs ghost" style="left:16px;top:2285px;font-size:108px;">FAQ</div>

<!-- PRICING -->
<svg class="abs" style="left:0;top:2385px" width="1200" height="410" viewBox="0 0 1200 410">
  <path d="M0 75 C300 20 800 0 1200 45 L1200 300 C900 280 300 300 0 380Z" fill="var(--duck)"/>
  <path d="M900 14 C1020 18 1120 30 1200 45" fill="none" stroke="var(--grey)" stroke-width="8"/>
  <path d="M0 380 C200 330 400 305 560 300" fill="none" stroke="var(--grey)" stroke-width="8"/>
</svg>
<div class="abs ghost" style="left:800px;top:2455px;font-size:108px;color:#8fbbc8;">PRICING</div>
<h2 class="abs center" style="top:2472px;color:#fff;">OUR PRICING</h2>
<div class="abs arrow-btn" style="left:139px;top:2726px;">‹</div>
<div class="abs arrow-btn" style="left:1028px;top:2726px;">›</div>

<div class="abs card" style="left:197px;top:2594px;width:250px;height:383px;">
  <div class="card-head" style="height:117px;background:linear-gradient(180deg,#9dbfca,#7ea7b4);font-size:17px;padding-top:28px;">Whole Body Cryotherapy</div>
  <svg class="abs" style="left:85px;top:63px" width="92" height="92"><circle cx="46" cy="46" r="42" fill="#fff" stroke="#7ea7b4" stroke-width="5"/><circle cx="46" cy="46" r="22" fill="none" stroke="#c6dfe6" stroke-width="7"/></svg>
  <span class="row" style="left:17px;top:183px;">SINGLE</span><span class="price" style="left:103px;top:180px;">$40</span><span class="buy" style="left:169px;top:181px;width:67px;">BUY NOW</span>
  <span class="row" style="left:17px;top:214px;">10 PACK</span><span class="price" style="left:103px;top:211px;">$380</span><span class="buy" style="left:169px;top:212px;width:67px;">BUY NOW</span>
  <span class="row" style="left:17px;top:245px;">20 PACK</span><span class="price" style="left:103px;top:242px;">$720</span><span class="buy" style="left:169px;top:243px;width:67px;">BUY NOW</span>
  <span class="row" style="left:17px;top:277px;">MONTHLY*</span><span class="price" style="left:103px;top:274px;">$400</span><span class="buy" style="left:169px;top:275px;width:67px;">BUY NOW</span>
  <div class="abs" style="left:17px;top:318px;width:216px;border-top:1px dashed #ddd;"></div>
  <div class="book" style="top:347px;font-size:14px;">BOOK A SESSION &nbsp;»</div>
</div>

<div class="abs card" style="left:752px;top:2594px;width:250px;height:383px;">
  <div class="card-head" style="height:117px;background:linear-gradient(180deg,#9dbfca,#7ea7b4);font-size:17px;padding-top:28px;">Cryo Facial</div>
  <svg class="abs" style="left:79px;top:63px" width="92" height="92"><circle cx="46" cy="46" r="42" fill="#fff" stroke="#7ea7b4" stroke-width="5"/><circle cx="46" cy="46" r="22" fill="none" stroke="#c6dfe6" stroke-width="7"/></svg>
  <span class="row" style="left:14px;top:183px;">SINGLE</span><span class="price" style="left:100px;top:180px;">$40</span><span class="buy" style="left:167px;top:181px;width:67px;">BUY NOW</span>
  <span class="row" style="left:14px;top:214px;">10 PACK</span><span class="price" style="left:100px;top:211px;">$380</span><span class="buy" style="left:167px;top:212px;width:67px;">BUY NOW</span>
  <span class="row" style="left:14px;top:245px;">20 PACK</span><span class="price" style="left:100px;top:242px;">$720</span><span class="buy" style="left:167px;top:243px;width:67px;">BUY NOW</span>
  <span class="row" style="left:14px;top:277px;">MONTHLY*</span><span class="price" style="left:100px;top:274px;">$400</span><span class="buy" style="left:167px;top:275px;width:67px;">BUY NOW</span>
  <div class="abs" style="left:17px;top:318px;width:216px;border-top:1px dashed #ddd;"></div>
  <div class="book" style="top:347px;font-size:14px;">BOOK A SESSION &nbsp;»</div>
</div>

<div class="abs card" style="left:448px;top:2566px;width:304px;height:437px;box-shadow:0 8px 20px rgba(0,0,0,.18);">
  <div class="card-head" style="height:132px;background:var(--grey);font-size:22px;padding-top:26px;">Local Cryotherapy</div>
  <svg class="abs" style="left:96px;top:75px" width="112" height="112"><circle cx="56" cy="56" r="51" fill="#fff" stroke="var(--grey)" stroke-width="5"/><circle cx="56" cy="56" r="27" fill="none" stroke="#c6dfe6" stroke-width="8"/></svg>
  <span class="row" style="left:36px;top:215px;">SINGLE</span><span class="price" style="left:122px;top:212px;">$40</span><span class="buy" style="left:188px;top:213px;width:69px;">BUY NOW</span>
  <span class="row" style="left:36px;top:246px;">10 PACK</span><span class="price" style="left:122px;top:243px;">$380</span><span class="buy" style="left:188px;top:244px;width:69px;">BUY NOW</span>
  <span class="row" style="left:36px;top:277px;">20 PACK</span><span class="price" style="left:122px;top:274px;">$720</span><span class="buy" style="left:188px;top:275px;width:69px;">BUY NOW</span>
  <span class="row" style="left:36px;top:309px;">MONTHLY*</span><span class="price" style="left:122px;top:306px;">$400</span><span class="buy" style="left:188px;top:307px;width:69px;">BUY NOW</span>
  <div class="abs" style="left:20px;top:352px;width:264px;border-top:1px dashed #ddd;"></div>
  <div class="book" style="top:396px;font-size:18px;color:var(--duck-dark);">BOOK A SESSION &nbsp;»</div>
</div>

<!-- TESTIMONIALS -->
<div class="abs ghost" style="left:0;top:3055px;font-size:108px;">TESTIMONI</div>
<h2 class="abs center" style="top:3086px;">TESTIMONIALS</h2>
<div class="abs arrow-btn" style="left:67px;top:3228px;border-color:#999;color:#999;">‹</div>
<div class="abs arrow-btn" style="left:1098px;top:3228px;border-color:#999;color:#999;">›</div>

<div class="abs avatar" style="left:130px;top:3174px;" role="img" aria-label="Client portrait"></div>
<p class="abs quote" style="left:217px;top:3181px;"><span class="mark">“</span>At vero eos et accusamus et iustodio dignissimos ducimus qui blanditiipraesnt ium voluptatum deleniti atq.</p>
<div class="abs who" style="left:217px;top:3264px;">Marisa Delane</div>
<div class="abs role" style="left:217px;top:3280px;">Financial Services Professional</div>
<div class="abs stars" style="left:215px;top:3315px;">★★★★☆</div>

<div class="abs avatar" style="left:455px;top:3174px;" role="img" aria-label="Client portrait"></div>
<p class="abs quote" style="left:545px;top:3181px;"><span class="mark">“</span>At vero eos et accusamus et iustodio dignissimos ducimus qui blanditiipraesnt ium voluptatum deleniti atqu.</p>
<div class="abs who" style="left:545px;top:3264px;">Tobias R. Lindqvist</div>
<div class="abs role" style="left:545px;top:3280px;">National Urban Fellow at the Harborview</div>
<div class="abs stars" style="left:543px;top:3315px;">★★★★★</div>

<div class="abs avatar" style="left:778px;top:3174px;" role="img" aria-label="Client portrait"></div>
<p class="abs quote" style="left:868px;top:3181px;"><span class="mark">“</span>At vero eos et accusamus et iustodio dignissimos ducimus qui blanditiipraesnt ium voluptatum deleniti atqu.</p>
<div class="abs who" style="left:868px;top:3264px;">Clara Whitfield</div>
<div class="abs role" style="left:868px;top:3280px;">Creative Strategist | Entrepreneur &amp; Upcoming</div>
<div class="abs stars" style="left:866px;top:3315px;">★★★★☆</div>

<!-- CONTACT -->
<svg class="abs" style="left:0;top:3400px" width="1200" height="624" viewBox="0 0 1200 624">
  <path d="M0 130 C300 40 750 10 1200 130 L1200 624 L0 624Z" fill="var(--grey)"/>
  <path d="M0 130 C300 40 750 10 1200 130" fill="none" stroke="#5e92d8" stroke-width="10"/>
  <path d="M120 80 C400 0 800 -5 1200 100" fill="none" stroke="#a9c7e6" stroke-width="9"/>
  <path d="M300 40 C600 -5 900 10 1200 70" fill="none" stroke="#d4e4f2" stroke-width="7"/>
</svg>
<div class="abs ghost" style="left:1062px;top:3998px;font-size:108px;color:#626262;transform:rotate(-90deg);transform-origin:0 0;">CONTACT</div>
<h2 class="abs center" style="top:3525px;color:#fff;">CONTACT US</h2>

<svg class="abs" style="left:149px;top:3617px" width="62" height="62" viewBox="0 0 62 62"><circle cx="31" cy="31" r="28" fill="#fff" stroke="var(--duck)" stroke-width="4"/><path d="M31 18a9 9 0 0 0-9 9c0 7 9 17 9 17s9-10 9-17a9 9 0 0 0-9-9z" fill="var(--grey)"/><circle cx="31" cy="27" r="3.5" fill="#fff"/></svg>
<div class="abs contact-head" style="left:223px;top:3613px;">NORTHBROOK</div>
<div class="abs contact-text" style="left:223px;top:3635px;">12 Harbor Lane<br>2nd Floor</div>
<div class="abs contact-head" style="left:223px;top:3687px;">HOURS</div>
<div class="abs contact-text" style="left:223px;top:3709px;">Monday - Friday 6:30 am - 8:00 pm<br>Saturday 8:00 am - 1:00 pm<br>Sunday Closed</div>
<div class="abs pill" style="left:223px;top:3789px;width:168px;height:38px;line-height:38px;background:var(--duck);font-size:12px;">BOOK A SESSION<span class="dot" style="width:10px;height:10px"></span></div>
<div class="abs link" style="left:223px;top:3844px;">DIRECTIONS</div>

<svg class="abs" style="left:461px;top:3617px" width="62" height="62" viewBox="0 0 62 62"><circle cx="31" cy="31" r="28" fill="#fff" stroke="var(--duck)" stroke-width="4"/><path d="M31 18a9 9 0 0 0-9 9c0 7 9 17 9 17s9-10 9-17a9 9 0 0 0-9-9z" fill="var(--grey)"/><circle cx="31" cy="27" r="3.5" fill="#fff"/></svg>
<div class="abs contact-head" style="left:536px;top:3613px;">EASTFIELD</div>
<div class="abs contact-text" style="left:536px;top:3635px;">450 Mill Street<br>3rd Floor</div>
<div class="abs contact-head" style="left:536px;top:3687px;">HOURS</div>
<div class="abs contact-text" style="left:536px;top:3709px;">Monday - Friday 6:00 am - 7:00 pm<br>Saturday Closed<br>Sunday Closed</div>
<div class="abs pill" style="left:536px;top:3789px;width:168px;height:38px;line-height:38px;background:var(--duck);font-size:12px;">BOOK A SESSION<span class="dot" style="width:10px;height:10px"></span></div>
<div class="abs link" style="left:536px;top:3844px;">DIRECTIONS</div>

<div class="abs brand" style="left:784px;top:3612px;color:#fff;font-size:36px;letter-spacing:6px;">GLACIA</div>
<svg class="abs" style="left:786px;top:3683px" width="62" height="62" viewBox="0 0 62 62"><circle cx="31" cy="31" r="28" fill="#fff" stroke="var(--duck)" stroke-width="4"/><path d="M22 19l6-2 4 8-4 3c2 4 5 7 9 9l3-4 8 4-2 6c-12 1-25-12-24-24z" fill="var(--grey)"/></svg>
<div class="abs contact-head" style="left:862px;top:3695px;font-size:14px;font-weight:600;">CALL US:</div>
<div class="abs contact-head" style="left:862px;top:3716px;font-size:18px;">555-014-2290</div>
<svg class="abs" style="left:786px;top:3771px" width="62" height="62" viewBox="0 0 62 62"><circle cx="31" cy="31" r="28" fill="#fff" stroke="var(--duck)" stroke-width="4"/><rect x="18" y="21" width="26" height="19" rx="2" fill="var(--grey)"/><path d="M18 23l13 10 13-10" fill="none" stroke="#fff" stroke-width="2"/></svg>
<div class="abs contact-head" style="left:862px;top:3782px;font-size:14px;font-weight:600;">EMAIL US :</div>
<div class="abs contact-head" style="left:862px;top:3803px;font-size:17px;">hello@glacia-studio.com</div>

<div class="abs social" style="left:511px;top:3912px;"></div>
<div class="abs social" style="left:558px;top:3912px;"></div>
<div class="abs social" style="left:603px;top:3912px;"></div>
<div class="abs social" style="left:651px;top:3912px;"></div>
<div class="abs center copy" style="top:3979px;">Copyrights © 2019, Companyname. All rights reserved &nbsp;|&nbsp; Privacy Policy &nbsp;|&nbsp; Terms of use</div>

</body>
</html>
```